Alaska Law Firm Needs a Sticker Design

We need a design for stickers to put on already-printed brochures. We mail the brochures to potential clients so they can learn more about accident-induced injuries, insurance claims, legal representation, and our own law firm.

One of our lawyers wrote a book that provides a helpful overview of personal injury claims. We are offering this book for free to anyone who calls and requests it. Therefore, the sticker design should include one of the following phrases, or something very similar:
a) "Still have questions? Call and request our book-- for free!"
b) "Still have questions about auto accident claims? Call and request our book today."
c) "Still have questions about filing a claim? Call and request a free copy of our book."
d) "Still have questions? Call us today to request a free copy of our book, Clear Lanes Ahead."
e) "To learn more about automobile accidents and insurance, call today and request a free copy of our book."

The sticker should be approximately 3"x3" and may be a circle, square, rectangle, or ellipsis. The sticker will be placed on the back of the folder, which is light blue. We would like the sticker to match the color scheme of our website and the folder.

I will upload an image of the book cover as soon as I obtain it.

Law Firm

Font styles to use
Serif
Sans Serif

Requirements
Should not have
• Bright colors that aren't already used in the folder design. e.g. no bright orange, pink, chartreuse, turquoise, yellow, red.

```html
<!DOCTYPE html>
<html lang="en">
<head>
<meta charset="utf-8">
<title>Still Have Questions Sticker</title>
<link rel="stylesheet" href="https://fonts.googleapis.com/css2?family=Rye&family=Kurale&display=swap">
<style>
  :root {
    --page-bg: #f2f2f3;
    --navy-deep: #15206a;
    --navy: #1f2f8f;
    --navy-bright: #23359e;
    --panel: #f7f7f8;
    --panel-shade: #e4e4e7;
    --ink: #262626;
    --white: #ffffff;
  }
  html, body {
    margin: 0;
    padding: 0;
    width: 1200px;
    height: 1200px;
    overflow: hidden;
    background: var(--page-bg);
  }
  .canvas {
    width: 1200px;
    height: 1200px;
    display: block;
  }
  .headline {
    font-family: "Rye", serif;
  }
  .headline--dark { fill: var(--ink); }
  .headline--blue { fill: var(--navy); }
  .headline--white { fill: var(--white); }
  .offer-line {
    font-family: "Kurale", serif;
    fill: var(--ink);
  }
  .offer-free {
    font-family: "Kurale", serif;
    fill: var(--navy);
  }
</style>
</head>
<body>
<svg class="canvas" viewBox="0 0 1300 1300" xmlns="http://www.w3.org/2000/svg">
  <defs>
    <linearGradient id="frameGradient" x1="0" y1="0" x2="0" y2="1">
      <stop offset="0" stop-color="var(--navy-bright)"/>
      <stop offset="0.5" stop-color="var(--navy-deep)"/>
      <stop offset="1" stop-color="var(--navy-bright)"/>
    </linearGradient>
    <linearGradient id="panelGradient" x1="0" y1="0" x2="0" y2="1">
      <stop offset="0" stop-color="var(--panel)"/>
      <stop offset="1" stop-color="var(--panel-shade)"/>
    </linearGradient>
    <filter id="stickerShadow" x="-10%" y="-10%" width="120%" height="120%">
      <feDropShadow dx="0" dy="6" stdDeviation="8" flood-color="#000" flood-opacity="0.25"/>
    </filter>
  </defs>

  <g class="sticker">
    <path class="sticker-frame" fill="url(#frameGradient)" filter="url(#stickerShadow)"
      d="M320,165 L980,165 C1080,215 1150,300 1140,420 C1130,480 1100,530 1080,560 L1175,630 L1150,730
         C1120,860 1000,960 820,1010 C720,1040 680,1100 650,1190 C620,1100 580,1040 480,1010
         C300,960 180,860 150,730 L125,630 L220,560 C200,530 170,480 160,420 C150,300 220,215 320,165 Z"/>

    <path class="sticker-panel-top" fill="url(#panelGradient)"
      d="M345,200 L955,200 C1050,245 1110,320 1100,420 C1095,480 1070,530 1040,568 L260,568
         C230,530 205,480 200,420 C190,320 250,245 345,200 Z"/>

    <path class="sticker-panel-bottom" fill="url(#panelGradient)"
      d="M175,732 L1125,732 C1100,850 990,940 820,985 C720,1015 675,1060 650,1140
         C625,1060 580,1015 480,985 C310,940 200,850 175,732 Z"/>

    <text class="headline headline--dark" x="652" y="365" font-size="140" text-anchor="middle"
      textLength="385" lengthAdjust="spacingAndGlyphs">STILL</text>
    <text class="headline headline--blue" x="650" y="517" font-size="140" text-anchor="middle"
      textLength="410" lengthAdjust="spacingAndGlyphs">HAVE</text>
    <text class="headline headline--white" x="668" y="700" font-size="140" text-anchor="middle"
      textLength="880" lengthAdjust="spacingAndGlyphs">QUESTIONS?</text>

    <text class="offer-line" x="667" y="795" font-size="46" text-anchor="middle"
      textLength="515" lengthAdjust="spacingAndGlyphs">Call and request our book</text>
    <text class="offer-free" x="658" y="925" font-size="112" text-anchor="middle"
      textLength="535" lengthAdjust="spacingAndGlyphs">FOR FREE!</text>
  </g>
</svg>
</body>
</html>
```